sydney wedding photography business needs a business card design

we need a business card design for a sydney based wedding photography and videography business. our business name is :golden hour studio and film. our target clients are 24-35 yrs female. our style is candid, organic, natural, dynamic. we are a team of young photographers and videographers, and help brides to create memories that they will cherish for the rest of their lives. the logo will be provided. we want an elegant design that reflects our style, and also want to give a great impression to our clients that we are one of the best studios in sydney and our brand means quality and premium service.

Target Market(s)

bride to be, 24-35 years old, living in sydney and surrunding areas

Industry/Entity Type

Wedding Photography

Contact Information for Business Card

address: 57 tarrant street, glenmore nsw 2047
mobile: 0431872259
phone: (02) 9163 2408
info@tidewillowstudio.net.au
www.tidewillowstudio.net.au
facebook:tidewillowweddings
instagram:tidewillowweddings

Font styles to use
Serif
Sans Serif

Requirements
Nice to have
• maybe add my slogan"memories beyond eternity" if the layout looks good
Should not have
• no black color, not good idea for wedding biz card

```html
<!DOCTYPE html>
<html lang="en">
<head>
<meta charset="utf-8">
<title>Golden Hour Studio and Film – Business Card</title>
<link href="https://fonts.googleapis.com/css2?family=Jost:wght@400;500;600&display=swap" rel="stylesheet">
<style>
  :root {
    --backdrop: #efeae1;
    --gold-light: #d9a514;
    --gold-mid: #c28f0e;
    --gold-deep: #9c6f08;
    --ink: #2a1c05;
    --card-bronze: #4a3319;
    --card-bronze-deep: #3a2713;
    --gold-text: #e6b02a;
    --title-cream: #eadfcb;
  }
  * { box-sizing: border-box; margin: 0; padding: 0; }
  html, body {
    width: 1200px; height: 774px; overflow: hidden;
    background: var(--backdrop);
    font-family: "Jost", "Futura", sans-serif;
  }
  .sheet {
    width: 1200px; height: 774px;
    display: flex; align-items: center; justify-content: center; gap: 44px;
  }
  .card {
    position: relative;
    width: 520px; height: 316px;
    border-radius: 3px;
    overflow: hidden;
    box-shadow: 0 6px 18px rgba(60, 45, 20, 0.18);
  }

  /* Contact side */
  .card--contact { color: var(--ink); }
  .card__pattern {
    position: absolute; inset: 0;
    background: radial-gradient(ellipse at 50% 30%, var(--gold-light) 0%, var(--gold-mid) 55%, var(--gold-deep) 100%);
  }
  .contact {
    position: relative; height: 100%;
    display: flex; flex-direction: column; align-items: center; justify-content: center;
    text-align: center; text-transform: uppercase;
    font-size: 14px; letter-spacing: 0.2px; line-height: 1.55;
    padding: 0 24px;
  }
  .contact__mark {
    width: 28px; height: 28px; border: 4px solid var(--ink); border-radius: 50%;
    margin-bottom: 16px;
  }
  .contact strong { font-weight: 600; }

  /* Name side */
  .card--name {
    background: radial-gradient(ellipse at 50% 40%, var(--card-bronze) 0%, var(--card-bronze-deep) 100%);
    display: flex; flex-direction: column; align-items: center; justify-content: center;
  }
  .brand {
    display: flex; align-items: center; gap: 12px;
    color: var(--gold-text);
  }
  .brand__dot {
    width: 14px; height: 14px; border-radius: 50%; background: var(--gold-text);
  }
  .brand__name {
    font-size: 36px; font-weight: 500; letter-spacing: 0.5px;
  }
  .brand__line {
    margin-top: 6px;
    font-size: 13px; font-weight: 500; letter-spacing: 8px;
    color: var(--gold-text); text-transform: uppercase;
  }
  .holder {
    margin-top: 40px;
    font-size: 18px; text-transform: uppercase; letter-spacing: 0.3px;
  }
  .holder__name { color: var(--gold-text); }
  .holder__role { color: var(--title-cream); font-size: 15px; }
</style>
</head>
<body>
<main class="sheet">
  <section class="card card--contact">
    <div class="card__pattern" role="img" aria-label="Gold background with a faint repeating ring pattern"></div>
    <div class="contact">
      <span class="contact__mark"></span>
      <p>57 Tarrant Street, Glenmore NSW 2047</p>
      <p><strong>Phone</strong> : (02) 9163 2408 &nbsp;<strong>Cell</strong> : (04) 3187 2259</p>
      <p>info@tidewillowstudio.net.au | www.tidewillowstudio.net.au</p>
      <p>tidewillowweddings</p>
    </div>
  </section>

  <section class="card card--name">
    <div class="brand">
      <span class="brand__dot"></span>
      <span class="brand__name">Golden Hour Studio</span>
    </div>
    <p class="brand__line">and film</p>
    <p class="holder">
      <span class="holder__name">Clara Hensley</span>
      <span class="holder__role"> – CEO/Founder</span>
    </p>
  </section>
</main>
</body>
</html>
```